Bright Pelvicare Business Card

Need a business card for a surgical practice called Bright Pelvicare. We have recently selected a logo (attached). The business card will need to have two formats:
1) One with the logo/physician name/ contact info on the front and location information on the back.
2) One in "appointment reminder card" style with the logo/ contact info/ date/ time on the front and the location information on the back.

The front side should include the following information:
- Logo
- Rohan K. Desai, MD FACOG
- phone: 469-555-0182
- fax: 1-469-555-0317
- email: admin@brightpelvi.com
- website: www.brightpelvicare.com

The back side should have the office locations listed:
4518 Kestrel Ave, Plano, TX 75198
3920 Bramwell Rd, Plano, TX 75147
2245 Silverpine Ln, Irving, TX 75163
815 W Garnet Ave S310, Dallas, TX 75284
3614 Lantern Blvd, Grand Prairie, TX 75179
7405 Amberly Crest Dr, San Antonio, TX 78391
5812 Tolliver Rd, Pasadena, TX 77639

Target Market(s)

1. Other physicians who might refer patients
2. Female patients

Industry/Entity Type

Business

Font styles to use
Other font styles liked:
• Tahoma for lettering

Requirements
Must have
• As per the instructions
Should not have
• No other images needed -- please try to keep font consistent with logo design. Can use Tahoma as the font for lettering.

```html
<!DOCTYPE html>
<html lang="en">
<head>
<meta charset="utf-8">
<title>Bright Pelvicare Business Card</title>
<link rel="stylesheet" href="https://fonts.googleapis.com/css2?family=Open+Sans:wght@400;600;700&family=Noto+Sans:wght@400&display=swap">
<style>
  :root {
    --page: #e9edf1;
    --navy: #1f4e8c;
    --teal: #35b0c0;
    --blue-light: #3cc0ec;
    --blue-mid: #1d8fd0;
    --blue-deep: #17509b;
    --white: #ffffff;
    --rule: #7d8aa0;
    --address: #1d3f73;
  }
  * { box-sizing: border-box; margin: 0; padding: 0; }
  html, body { width: 1200px; height: 793px; overflow: hidden; }
  body {
    background: var(--page);
    font-family: "Open Sans", Tahoma, sans-serif;
    position: relative;
  }
  .card {
    position: absolute;
    left: 308px;
    width: 561px;
    height: 325px;
    overflow: hidden;
    background: radial-gradient(ellipse 70% 85% at 50% 20%, var(--blue-light) 0%, var(--blue-mid) 45%, var(--blue-deep) 100%);
    box-shadow: 0 3px 10px rgba(0,0,0,.25);
  }
  .card--front { top: 63px; }
  .card--back { top: 414px; }

  /* front */
  .brand-panel {
    position: absolute;
    left: 0; top: 10px;
    width: 100%; height: 161px;
    background: var(--white);
    display: flex; align-items: center; justify-content: center;
  }
  .brand-name {
    font-weight: 600;
    font-size: 34px;
    color: var(--navy);
    letter-spacing: .3px;
    margin-top: 30px;
  }
  .brand-notch {
    position: absolute;
    left: 50%; top: 171px;
    transform: translateX(-50%);
  }
  .physician {
    position: absolute;
    left: 0; top: 211px; width: 100%;
    text-align: center;
    color: var(--white);
  }
  .physician__name { font-size: 24px; font-weight: 400; line-height: 32px; }
  .physician__title { font-size: 14.5px; line-height: 22px; margin-top: 1px; }

  /* back */
  .contact {
    position: absolute;
    left: 0; top: 16px; width: 100%;
    text-align: center;
    color: var(--white);
    font-size: 15px;
    line-height: 19px;
  }
  .contact b { font-weight: 700; }
  .contact__item { margin: 0 9px; }
  .appointment {
    position: absolute;
    left: 23px; top: 68px;
    width: 517px; height: 36px;
    background: var(--white);
    display: flex; align-items: stretch;
    font-size: 12.5px;
    color: var(--navy);
  }
  .appointment__label {
    width: 113px;
    background: var(--teal);
    color: var(--white);
    font-weight: 600;
    font-size: 15px;
    display: flex; align-items: center; justify-content: center;
  }
  .appointment__fields {
    flex: 1;
    position: relative;
  }
  .appointment__rule {
    position: absolute;
    left: 10px; right: 12px; top: 25px;
    border-top: 1px solid var(--rule);
  }
  .field { position: absolute; top: 8px; }
  .field--date { left: 12px; }
  .field--time { left: 181px; }
  .field--am { left: 307px; font-size: 11px; top: 10px; }
  .field--pm { left: 355px; font-size: 11px; top: 10px; }
  .tick-box {
    display: inline-block;
    width: 10px; height: 10px;
    border: 1px solid var(--navy);
    margin-right: 5px;
    vertical-align: -1px;
  }
  .locations {
    position: absolute;
    left: 23px; top: 115px;
    width: 517px; height: 189px;
    background: var(--white);
    list-style: none;
    padding: 7px 0 0 64px;
    font-family: "Noto Sans", Verdana, sans-serif;
    font-size: 17.5px;
    letter-spacing: .9px;
    color: var(--address);
  }
  .locations li {
    height: 25.6px;
    line-height: 25.6px;
    display: flex; align-items: center;
  }
  .locations li::before {
    content: "";
    width: 11px; height: 11px;
    border: 1.5px solid var(--blue-mid);
    border-radius: 50%;
    margin-right: 10px;
    flex: none;
  }
</style>
</head>
<body>

<section class="card card--front" aria-label="Business card front">
  <div class="brand-panel">
    <span class="brand-name">Bright Pelvicare</span>
  </div>
  <svg class="brand-notch" width="36" height="18" viewBox="0 0 36 18" aria-hidden="true">
    <polygon points="0,0 36,0 18,18" fill="#ffffff"/>
  </svg>
  <div class="physician">
    <p class="physician__name">Rohan K. Desai. MD FACOG</p>
    <p class="physician__title">Female Pelvic Medicine &amp; Reconstructive Surgery</p>
  </div>
</section>

<section class="card card--back" aria-label="Business card back">
  <div class="contact">
    <p><span class="contact__item"><b>phone</b>: 469-555-0182</span><span class="contact__item"><b>fax</b>: 1-469-555-0317</span></p>
    <p><span class="contact__item"><b>email</b>: admin@brightpelvi.com</span><span class="contact__item"><b>website</b>: www.brightpelvicare.com</span></p>
  </div>

  <div class="appointment">
    <div class="appointment__label">Appointment</div>
    <div class="appointment__fields">
      <span class="field field--date">Date:</span>
      <span class="field field--time">Time:</span>
      <span class="field field--am"><span class="tick-box"></span>am</span>
      <span class="field field--pm"><span class="tick-box"></span>pm</span>
      <span class="appointment__rule"></span>
    </div>
  </div>

  <ul class="locations">
    <li>4518 Kestrel Ave, Plano, TX 75198</li>
    <li>3920 Bramwell Rd, Plano, TX 75147</li>
    <li>2245 Silverpine Ln, Irving, TX 75163</li>
    <li>815 W Garnet Ave S310, Dallas, TX 75284</li>
    <li>3614 Lantern Blvd, Grand Prairie, TX 75179</li>
    <li>7405 Amberly Crest Dr, San Antonio, TX 78391</li>
    <li>5812 Tolliver Rd, Pasadena, TX 77639</li>
  </ul>
</section>

</body>
</html>
```